Velvet Dice Night Age Verification Landing Page

To create a visually appealing design for the landing page of the adult game "Velvet Dice Night" that confirms the visitor's age.
The design should have a simple and visually appealing look that focuses on two buttons labeled "Yes" and "No". The purpose of the page is to confirm that the visitor is 18 years of age or older before accessing the game's content. Responsive design that works well on desktop and mobile devices. The final output should be delivered in PSD, AI, or Sketch format, along with any necessary images or assets.
I have also attached examples.

```html
<!DOCTYPE html>
<html lang="en">
<head>
<meta charset="utf-8">
<title>Velvet Dice Night – Age Verification</title>
<link rel="stylesheet" href="https://fonts.googleapis.com/css2?family=Montserrat:wght@500;600;700&family=Yellowtail&display=swap">
<style>
  :root {
    --bg-dark: #24252b;
    --photo-warm: #6b4a45;
    --photo-red: #7a2a2e;
    --panel-purple: #4b2a70;
    --accent-blue: #3f8fc4;
    --accent-violet: #8a4fe0;
    --accent-ice: #9fd8f0;
    --brand-pink: #c67fd8;
    --text-white: #ffffff;
    --button-text: #2a1840;
    --line-violet: #7a4fd0;
  }
  * { box-sizing: border-box; margin: 0; padding: 0; }
  html, body { width: 1067px; height: 1200px; overflow: hidden; background: var(--bg-dark); }
  .page {
    position: relative;
    width: 1067px;
    height: 1200px;
    overflow: hidden;
    font-family: "Montserrat", sans-serif;
    color: var(--text-white);
    background: var(--bg-dark);
  }
  .hero-photo {
    position: absolute;
    inset: 0;
    background:
      radial-gradient(ellipse 300px 380px at 560px 330px, var(--photo-warm) 0%, rgba(107,74,69,0.4) 55%, transparent 100%),
      radial-gradient(ellipse 260px 220px at 330px 420px, var(--photo-red) 0%, transparent 100%),
      radial-gradient(ellipse 320px 400px at 820px 250px, rgba(120,80,70,0.55) 0%, transparent 100%),
      linear-gradient(180deg, #2c2d33 0%, #24252b 60%, #1d1e22 100%);
    filter: blur(6px);
  }
  .brand {
    position: absolute;
    top: 48px;
    left: 0;
    width: 100%;
    display: flex;
    justify-content: center;
    align-items: center;
    gap: 14px;
  }
  .brand-dot {
    width: 22px; height: 22px; border-radius: 50%;
    background: var(--brand-pink);
  }
  .brand-name {
    font-family: "Montserrat", sans-serif;
    font-weight: 600;
    font-size: 34px;
    color: var(--brand-pink);
    letter-spacing: 0.5px;
  }
  .music-toggle {
    position: absolute;
    left: 973px; top: 16px;
    width: 51px; height: 48px;
    border: 2px solid var(--text-white);
    border-radius: 9px;
    display: flex; align-items: center; justify-content: center;
  }
  .bubble-shape { position: absolute; inset: 0; }
  .verify-card {
    position: absolute;
    left: 84px; top: 460px;
    width: 872px; height: 429px;
    border: 2px dotted rgba(255,255,255,0.85);
    text-align: center;
  }
  .verify-title {
    font-family: "Yellowtail", cursive;
    font-weight: 400;
    font-size: 118px;
    line-height: 1;
    margin-top: 42px;
    color: var(--text-white);
  }
  .verify-question {
    font-size: 27px;
    font-weight: 500;
    margin-top: 46px;
  }
  .verify-actions {
    display: flex;
    justify-content: center;
    gap: 8px;
    margin-top: 32px;
  }
  .verify-button {
    width: 147px; height: 60px;
    background: var(--text-white);
    color: var(--button-text);
    font-family: "Montserrat", sans-serif;
    font-weight: 600;
    font-size: 21px;
    letter-spacing: 1px;
    border: 0;
    display: flex; align-items: center; justify-content: center;
  }
  .remember {
    display: flex;
    justify-content: center;
    align-items: center;
    gap: 10px;
    margin-top: 36px;
    font-size: 17px;
    font-weight: 500;
  }
  .remember-box {
    width: 18px; height: 18px;
    background: #e8e8ee;
    border-radius: 3px;
  }
</style>
</head>
<body>
<main class="page">
  <div class="hero-photo" role="img" aria-label="Blurred background photo of a smiling woman with red hair in a dark jacket"></div>

  <header class="brand">
    <span class="brand-dot"></span>
    <span class="brand-name">Velvet Dice Night</span>
  </header>

  <div class="music-toggle" aria-label="Toggle music">
    <svg width="26" height="28" viewBox="0 0 26 28" aria-hidden="true">
      <path d="M9 4 L23 1 L23 19" fill="none" stroke="#fff" stroke-width="2.6"/>
      <line x1="9" y1="4" x2="9" y2="22" stroke="#fff" stroke-width="2.6"/>
      <ellipse cx="5.5" cy="22.5" rx="4.5" ry="3.6" fill="#fff"/>
      <ellipse cx="19.5" cy="19.5" rx="4.5" ry="3.6" fill="#fff"/>
    </svg>
  </div>

  <svg class="bubble-shape" width="1067" height="1200" viewBox="0 0 1067 1200" aria-hidden="true">
    <path d="M60 433 H990 Q1022 433 1022 465 V895 Q1022 927 990 927 H855 L700 1044 L667 927 H60 Z" fill="var(--accent-blue)"/>
    <rect x="60" y="433" width="920" height="483" fill="var(--panel-purple)"/>
    <polygon points="690,915 822,915 706,1012" fill="var(--panel-purple)"/>
    <g class="rule-lines">
      <line x1="60" y1="949" x2="638" y2="949" stroke="#ffffff" stroke-width="2"/>
      <line x1="60" y1="958" x2="638" y2="958" stroke="var(--line-violet)" stroke-width="2"/>
      <line x1="60" y1="967" x2="638" y2="967" stroke="#ffffff" stroke-width="2"/>
      <line x1="60" y1="976" x2="638" y2="976" stroke="var(--line-violet)" stroke-width="2"/>
      <line x1="60" y1="985" x2="638" y2="985" stroke="#ffffff" stroke-width="2"/>
      <line x1="60" y1="993" x2="638" y2="993" stroke="var(--line-violet)" stroke-width="2"/>
    </g>
    <g class="sparkles">
      <rect x="507" y="403" width="26" height="26" transform="rotate(45 520 416)" fill="var(--accent-violet)"/>
      <rect x="182" y="422" width="10" height="10" transform="rotate(45 187 427)" fill="#ffffff"/>
      <rect x="869" y="415" width="14" height="14" transform="rotate(45 876 422)" fill="var(--accent-ice)"/>
      <rect x="48" y="641" width="24" height="24" transform="rotate(45 60 653)" fill="var(--accent-violet)"/>
      <rect x="992" y="628" width="16" height="16" transform="rotate(45 1000 636)" fill="#ffffff"/>
      <rect x="341" y="910" width="24" height="24" transform="rotate(45 353 922)" fill="var(--accent-violet)"/>
    </g>
  </svg>

  <section class="verify-card">
    <h1 class="verify-title">Dirty Games</h1>
    <p class="verify-question">Are you over 18 Years of age?</p>
    <div class="verify-actions">
      <span class="verify-button">YES</span>
      <span class="verify-button">NO</span>
    </div>
    <div class="remember">
      <span class="remember-box"></span>
      <span>Remember Me?</span>
    </div>
  </section>
</main>
</body>
</html>
```